business card deign

Logo needs the following on it.
1. attached logo
2. Tagline - "From cold coolers to loud speakers...we bring the fun!"
3. Name- Dalton Pikes, Founder and CPO
4. Address - 412 E. Carver Avenue, Ste 2207, Tampa, FL. 33917
5. Phone - 555.318.4726

```html
<!DOCTYPE html>
<html lang="en">
<head>
<meta charset="utf-8">
<title>Chillbound Business Card</title>
<link rel="stylesheet" href="https://fonts.googleapis.com/css2?family=Roboto:wght@400;500;700;900&display=swap">
<style>
  :root {
    --backdrop: #d9bfa3;
    --card: #ffffff;
    --ink: #111111;
    --ink-soft: #2a2a2a;
    --art-dark: #161616;
    --art-light: #f6f6f6;
    --shadow: rgba(60, 35, 15, 0.28);
  }
  * { box-sizing: border-box; margin: 0; padding: 0; }
  html, body {
    width: 1200px;
    height: 711px;
    overflow: hidden;
  }
  body {
    background: var(--backdrop);
    font-family: "Roboto", Arial, sans-serif;
    color: var(--ink);
    position: relative;
  }
  .card {
    position: absolute;
    top: 200px;
    width: 540px;
    height: 310px;
    background: var(--card);
    border-radius: 22px;
    box-shadow: 0 14px 30px var(--shadow);
    overflow: hidden;
  }
  .card-front { left: 40px; }
  .card-back { left: 620px; }

  /* Front */
  .front-brand {
    position: absolute;
    inset: 0;
    display: flex;
    align-items: center;
    justify-content: center;
    gap: 18px;
  }
  .brand-mark {
    width: 34px;
    height: 34px;
    background: var(--ink);
  }
  .brand-name {
    font-weight: 900;
    font-size: 44px;
    letter-spacing: 11px;
    text-transform: uppercase;
    color: var(--ink);
  }

  /* Back */
  .back-info {
    position: absolute;
    left: 30px;
    top: 36px;
    width: 260px;
    z-index: 1;
  }
  .back-brand {
    display: flex;
    align-items: center;
    gap: 9px;
    margin-bottom: 28px;
  }
  .back-brand .brand-mark { width: 16px; height: 16px; }
  .back-brand .brand-name { font-size: 19px; letter-spacing: 5px; }
  .identity {
    border-left: 9px solid var(--ink);
    margin-left: -30px;
    padding-left: 21px;
    margin-bottom: 14px;
  }
  .person-name {
    font-weight: 700;
    font-size: 26px;
    line-height: 1.1;
  }
  .person-role {
    font-size: 14px;
    font-weight: 500;
    margin-top: 3px;
  }
  .tagline {
    font-size: 11.5px;
    line-height: 1.45;
    color: var(--ink-soft);
    margin-bottom: 12px;
    max-width: 200px;
  }
  .contact-list { list-style: none; }
  .contact-item {
    display: flex;
    align-items: flex-start;
    gap: 8px;
    font-size: 11.5px;
    line-height: 1.45;
    color: var(--ink-soft);
  }
  .contact-item + .contact-item { margin-top: 3px; }
  .contact-item svg { flex: none; margin-top: 2px; }
  .back-art {
    position: absolute;
    right: 0;
    top: 0;
    width: 250px;
    height: 100%;
    background: linear-gradient(100deg, var(--card) 0%, var(--art-light) 30%, #cfcfcf 55%, #3a3a3a 78%, var(--art-dark) 100%);
  }
</style>
</head>
<body>
  <section class="card card-front" aria-label="Card front">
    <div class="front-brand">
      <span class="brand-mark" aria-hidden="true"></span>
      <span class="brand-name">Chillbound</span>
    </div>
  </section>

  <section class="card card-back" aria-label="Card back">
    <div class="back-art" role="img" aria-label="Large white animal silhouette set against a black background"></div>
    <div class="back-info">
      <div class="back-brand">
        <span class="brand-mark" aria-hidden="true"></span>
        <span class="brand-name">Chillbound</span>
      </div>
      <div class="identity">
        <p class="person-name">Dalton Pikes</p>
        <p class="person-role">Founder and CPO</p>
      </div>
      <p class="tagline">From cold coolers to loud speakers...we bring the fun!</p>
      <ul class="contact-list">
        <li class="contact-item">
          <svg width="11" height="11" viewBox="0 0 24 24" aria-hidden="true"><path fill="#111" d="M6.6 10.8a15.5 15.5 0 0 0 6.6 6.6l2.2-2.2a1 1 0 0 1 1-.25 11.4 11.4 0 0 0 3.6.57 1 1 0 0 1 1 1V20a1 1 0 0 1-1 1A17 17 0 0 1 3 4a1 1 0 0 1 1-1h3.5a1 1 0 0 1 1 1c0 1.25.2 2.45.57 3.6a1 1 0 0 1-.25 1z"/></svg>
          <span>555.318.4726</span>
        </li>
        <li class="contact-item">
          <svg width="11" height="13" viewBox="0 0 24 28" aria-hidden="true"><path fill="#111" d="M12 0a9 9 0 0 0-9 9c0 6.75 9 17 9 17s9-10.25 9-17a9 9 0 0 0-9-9zm0 12.5A3.5 3.5 0 1 1 12 5.5a3.5 3.5 0 0 1 0 7z"/></svg>
          <span>412 E. Carver Avenue,<br>Ste 2207, Tampa, FL. 33917</span>
        </li>
      </ul>
    </div>
  </section>
</body>
</html>
```